New Business Card Design Project

We require a business card design for Vexalund, a newly established Indian company.
Our focus is on the development, manufacturing, and export of a diverse array of pharmaceutical products on a global scale. The card should convey a professional appearance, as our primary markets are in Africa, China, and Southeast Asian nations.
We envision a two-sided business card, with the reverse side dedicated to a logo set against a solid color or an elegantly designed pattern. The corners should be rounded. We would appreciate seeing both horizontal and vertical design options. We trust the designer to utilize their expertise in creating this design.

The content for the business card is included in the attached Word file.

Target Market(s)

Our primary markets are in Africa, China, and Southeast Asian, Latin America, Maldives, Sri Lanka

Industry/Entity Type

Pharmaceutical Manufacturing and Export

Contact Information for Business Card

Colors

Designer to choose colors to be used in the design.

Requirements
Must have
• The reverse side of the business card features solely the logo along with the tagline, "Care Beyond Borders."
Should not have
• The logo should not exceed two instances, encompassing both the front and back sides of the card.

```html
<!DOCTYPE html>
<html lang="en">
<head>
<meta charset="utf-8">
<title>Vexalund Business Card</title>
<link href="https://fonts.googleapis.com/css2?family=Montserrat:wght@400;500;700;800&display=swap" rel="stylesheet">
<style>
  :root {
    --brand-blue: #29a5df;
    --ink: #1d1d1f;
    --paper: #ffffff;
    --backdrop: #e9e6e1;
    --card-shadow: rgba(0, 0, 0, 0.22);
  }
  * { box-sizing: border-box; margin: 0; padding: 0; }
  html, body {
    width: 1200px; height: 931px; overflow: hidden;
    background: var(--backdrop);
    font-family: "Montserrat", sans-serif;
  }
  .canvas { position: relative; width: 1200px; height: 931px; }
  .card {
    position: absolute;
    width: 620px; height: 354px;
    border-radius: 24px;
    box-shadow: 0 10px 28px var(--card-shadow);
    overflow: hidden;
  }
  .card-back { left: 100px; top: 80px; background: var(--brand-blue); }
  .card-front { left: 480px; top: 480px; background: var(--paper); }

  .back-wordmark {
    position: absolute; left: 150px; top: 218px;
    color: var(--paper);
    text-align: right;
  }
  .back-wordmark .name { font-weight: 800; font-size: 60px; line-height: 1; letter-spacing: 0.5px; }
  .back-wordmark .tagline { font-weight: 700; font-size: 19px; margin-top: 8px; letter-spacing: 0.5px; }

  .front-brand {
    position: absolute; right: 60px; top: 48px;
    display: flex; align-items: center; gap: 10px;
    color: var(--brand-blue); font-weight: 800; font-size: 38px; line-height: 1;
  }
  .front-brand .dot { width: 14px; height: 14px; border-radius: 50%; background: var(--brand-blue); }

  .person { position: absolute; left: 96px; top: 136px; }
  .person .person-name { color: var(--brand-blue); font-weight: 800; font-size: 30px; line-height: 1; }
  .person .role { margin-top: 10px; margin-left: 4px; color: var(--ink); font-weight: 500; font-size: 16px; line-height: 1; }

  .divider {
    position: absolute; left: 96px; right: 36px; top: 206px;
    height: 2px; background: var(--brand-blue);
  }

  .address {
    position: absolute; right: 40px; top: 222px;
    text-align right; text-align: right; color: var(--ink); font-size: 13px; line-height: 1.45;
  }
  .contacts { position: absolute; left: 96px; top: 232px; list-style: none; }
  .contacts li {
    display: flex; align-items: center; gap: 12px;
    color: var(--ink); font-size: 15px; line-height: 1; margin-bottom: 13px;
  }
  .contacts svg { width: 16px; height: 16px; fill: var(--brand-blue); flex: none; }
</style>
</head>
<body>
<div class="canvas">
  <section class="card card-back" aria-label="Card reverse">
    <div class="back-wordmark">
      <div class="name">Vexalund</div>
      <div class="tagline">Care Beyond Borders</div>
    </div>
  </section>

  <section class="card card-front" aria-label="Card front">
    <div class="front-brand"><span class="dot"></span>Vexalund</div>
    <div class="person">
      <div class="person-name">Rohan K. Desai</div>
      <div class="role">CEO</div>
    </div>
    <div class="divider"></div>
    <div class="address">12, Sunrise Colony,<br>Nagpur, 440010, India</div>
    <ul class="contacts">
      <li>
        <svg viewBox="0 0 16 16" aria-hidden="true"><path d="M3.5 1.5l2.5 0 1 3.5-1.8 1.3a8 8 0 0 0 4.5 4.5l1.3-1.8 3.5 1v2.5c0 .8-.7 1.5-1.5 1.5A12.5 12.5 0 0 1 2 3c0-.8.7-1.5 1.5-1.5z"/></svg>
        +919876500123
      </li>
      <li>
        <svg viewBox="0 0 16 16" aria-hidden="true"><path d="M1 3h14v10H1z"/><path d="M1.5 3.5 8 9l6.5-5.5" stroke="#fff" stroke-width="1.2" fill="none"/></svg>
        desai@vexalund.com
      </li>
      <li>
        <svg viewBox="0 0 16 16" aria-hidden="true"><circle cx="8" cy="8" r="7"/><path d="M1 8h14M8 1c2.5 2.5 2.5 11.5 0 14M8 1c-2.5 2.5-2.5 11.5 0 14" stroke="#fff" stroke-width="1" fill="none"/></svg>
        www.vexalund.com
      </li>
    </ul>
  </section>
</div>
</body>
</html>
```